Dog treat bakery needs updated bag labels

We're a small-batch dog treat bakery and would like to update our front bag labels to 1) differentiate our line of products and 2) to stand out on shelves. We believe all dogs deserve to eat clean, healthy foods. That's why we bake low-calorie, clean treats made with simple, premium ingredients like teff, amaranth, and sorghum flours and 100% blueberry, carrot, and purple sweet potato. All our treats are made gluten free without preservatives, artificial flavors, soy, corn, wheat, or eggs. Clean treats, happy dogs!

Logo Text

see uploaded files

```html
<!DOCTYPE html>
<html lang="en">
<head>
<meta charset="utf-8">
<title>Wiggle Pup – Maple's Bites Label</title>
<link rel="stylesheet" href="https://fonts.googleapis.com/css2?family=Oswald:wght@400;500&family=Libre+Baskerville:wght@400;700&display=swap">
<style>
  :root {
    --teal: #1a9ea5;
    --teal-soft: #5cbcc1;
    --charcoal: #323232;
    --white: #ffffff;
    --brown: #9a4a22;
    --page: #f4f4f4;
  }
  html, body {
    margin: 0;
    width: 1200px;
    height: 2581px;
    overflow: hidden;
    background: var(--page);
  }
  .label {
    position: absolute;
    left: 83px;
    top: 992px;
    width: 1030px;
    height: 596px;
    background: var(--teal);
    overflow: hidden;
  }
  .label svg.front-panel {
    position: absolute;
    left: 0;
    top: 0;
  }
  .hearts-art {
    position: absolute;
    left: 30px;
    top: 45px;
    width: 265px;
    height: 515px;
    border-radius: 40px;
    background: linear-gradient(180deg, var(--teal-soft), var(--teal));
  }
  .center-text {
    position: absolute;
    left: 277px;
    width: 446px;
    text-align: center;
    margin: 0;
  }
  .gluten-free {
    top: 18px;
    font: 700 28px "Libre Baskerville", serif;
    color: var(--teal);
    letter-spacing: 1px;
  }
  .product-type {
    top: 58px;
    font: 500 56px "Oswald", sans-serif;
    color: var(--white);
    letter-spacing: 1px;
  }
  .brand {
    top: 268px;
    font: 700 34px "Libre Baskerville", serif;
    color: var(--brown);
  }
  .tagline {
    top: 318px;
    font: 400 17px "Libre Baskerville", serif;
    color: var(--teal);
  }
  .product-name {
    top: 492px;
    font: 700 36px "Libre Baskerville", serif;
    color: var(--teal);
    letter-spacing: 1px;
  }
  .net-weight {
    top: 545px;
    font: 700 18px "Libre Baskerville", serif;
    color: var(--white);
  }
  .claims {
    position: absolute;
    left: 774px;
    top: 58px;
    margin: 0;
    font: 400 29px/43px "Oswald", sans-serif;
    color: var(--charcoal);
    text-transform: uppercase;
  }
  .claims p { margin: 0 0 40px; }
  .calorie-pill {
    position: absolute;
    left: 728px;
    top: 500px;
    width: 243px;
    height: 60px;
    border-radius: 30px;
    background: var(--charcoal);
    color: var(--white);
    font: 400 27px/60px "Oswald", sans-serif;
    text-align: center;
  }
</style>
</head>
<body>
  <section class="label">
    <div class="hearts-art" role="img" aria-label="Hand-drawn white outline hearts scattered down the left side"></div>

    <svg class="front-panel" width="1030" height="596" viewBox="0 0 1030 596" aria-hidden="true">
      <path fill="var(--charcoal)" d="M357,0 L653,0 C650,120 690,170 705,225 L717,260 L717,380 C690,440 650,480 653,596 L357,596 C360,480 310,440 293,380 L277,350 L277,260 C300,200 360,120 357,0 Z"/>
      <circle cx="500" cy="303" r="165" fill="var(--white)"/>
    </svg>

    <p class="center-text gluten-free">gluten free</p>
    <p class="center-text product-type">DOG TREATS</p>
    <p class="center-text brand">Wiggle Pup</p>
    <p class="center-text tagline">Clean treats, Happy dogs!</p>
    <p class="center-text product-name">Maple’s Bites</p>
    <p class="center-text net-weight">Net Wt 4 OZ (113g)</p>

    <div class="claims">
      <p>No<br>Soy, Corn,<br>Wheat, Eggs<br>or Dairy</p>
      <p>Made with<br>Ancient Grains<br>and Grass Fed<br>Beef Liver</p>
    </div>

    <div class="calorie-pill">10 CALORIES EACH</div>
  </section>
</body>
</html>
```